U.S. Popcorn company needs business cards

We are a popcorn company that manufactures popcorn and sells it to grocery stores worldwide. Our theme is "Americana" and our logo is U.S. route 66 which is the most famous highway in the U.S.

We would like the design to be simple and to use both sides. On the back side we would like to see just the logo and website. The front would be normal details

Target Market(s)

Wholesalers, grocers and distributors

Industry/Entity Type

Manufacture

Contact Information for Business Card

Business name: Prairie Lantern Popcorn
Phone: +1 555 308 4726
Email: Dale@prairielanternpopcorn.com
website: www.prairielanternpopcorn.com
Tag Line: "Fresh from the prairie"
Name: Dale Whitcombe
Title: Founder/President

Requirements
Must have
• Either this design should be fun or clean and simple. I will let you show me your thougths.
Nice to have
• Anything that ties in the real Hwy Route 66.
• Colors might need to be red, white and blue incorporated.
Should not have
• Not be too busy.

```html
<!DOCTYPE html>
<html lang="en">
<head>
<meta charset="utf-8">
<title>Prairie Lantern Popcorn – Business Card</title>
<link rel="stylesheet" href="https://fonts.googleapis.com/css2?family=Lato:wght@400;700&display=swap">
<style>
  :root {
    --navy: #222e63;
    --red: #e02327;
    --white: #ffffff;
    --backdrop: #e9e6e1;
    --shadow: rgba(0, 0, 0, 0.18);
  }
  * { margin: 0; padding: 0; box-sizing: border-box; }
  html, body {
    width: 1200px;
    height: 902px;
    overflow: hidden;
    background: var(--backdrop);
    font-family: "Lato", Arial, sans-serif;
  }
  .card {
    position: absolute;
    left: 100px;
    top: 165px;
    width: 1000px;
    height: 571px;
    border-radius: 24px;
    overflow: hidden;
    background: var(--white);
    box-shadow: 0 10px 30px var(--shadow);
  }
  .card-shapes {
    position: absolute;
    inset: 0;
    width: 100%;
    height: 100%;
  }
  .details {
    position: absolute;
    left: 44px;
    top: 0;
    color: var(--white);
  }
  .company-name {
    position: absolute;
    top: 56px;
    left: 0;
    white-space: nowrap;
    font-size: 36px;
    font-weight: 700;
    letter-spacing: 0.2px;
  }
  .tagline {
    position: absolute;
    top: 110px;
    left: 0;
    white-space: nowrap;
    font-size: 23px;
    font-weight: 400;
  }
  .person-name {
    position: absolute;
    top: 198px;
    left: 0;
    white-space: nowrap;
    font-size: 37px;
    font-weight: 400;
  }
  .person-title {
    position: absolute;
    top: 240px;
    left: 0;
    white-space: nowrap;
    font-size: 25px;
    color: var(--red);
  }
  .location {
    position: absolute;
    top: 320px;
    left: 2px;
    white-space: nowrap;
    font-size: 25px;
    line-height: 34px;
  }
  .contact-list {
    position: absolute;
    top: 404px;
    left: 2px;
    list-style: none;
  }
  .contact-item {
    display: flex;
    align-items: center;
    height: 33px;
    white-space: nowrap;
    font-size: 24px;
  }
  .contact-icon {
    width: 26px;
    height: 26px;
    margin-right: 14px;
    flex: none;
  }
  .brand-mark {
    position: absolute;
    left: 560px;
    top: 170px;
    width: 390px;
    display: flex;
    flex-direction: column;
    align-items: center;
    gap: 18px;
  }
  .brand-dot {
    width: 58px;
    height: 58px;
    border-radius: 50%;
    background: var(--red);
  }
  .brand-name {
    color: var(--navy);
    font-size: 40px;
    font-weight: 700;
    line-height: 46px;
    text-align: center;
  }
</style>
</head>
<body>
  <div class="card">
    <svg class="card-shapes" viewBox="0 0 1000 571" aria-hidden="true">
      <path d="M0 0 H522 Q428 285.5 522 571 H0 Z" fill="var(--navy)"/>
      <path d="M527 0 Q436 285.5 527 571 L533 571 Q446 285.5 533 0 Z" fill="var(--red)"/>
    </svg>

    <section class="details">
      <h1 class="company-name">Prairie Lantern Popcorn</h1>
      <p class="tagline">Fresh from the prairie</p>
      <h2 class="person-name">Dale Whitcombe</h2>
      <p class="person-title">Founder/President</p>
      <p class="location">Cedar Hollow, KS<br>United States</p>
      <ul class="contact-list">
        <li class="contact-item">
          <svg class="contact-icon" viewBox="0 0 26 26" aria-hidden="true">
            <rect width="26" height="26" rx="4" fill="var(--red)"/>
            <path d="M8 6 L11 6 L12 10 L10 11.5 Q12 15 14.5 16 L16 14 L20 15 L20 18 Q19 20 16.5 20 Q7 18 6 8.5 Q6 6 8 6 Z" fill="var(--navy)"/>
          </svg>
          +1 555 308 4726
        </li>
        <li class="contact-item">
          <svg class="contact-icon" viewBox="0 0 26 26" aria-hidden="true">
            <rect width="26" height="26" rx="4" fill="var(--red)"/>
            <rect x="5" y="8" width="16" height="11" fill="var(--navy)"/>
            <path d="M5 8 L13 14 L21 8" fill="none" stroke="var(--red)" stroke-width="1.4"/>
          </svg>
          Dale@prairielanternpopcorn.com
        </li>
        <li class="contact-item">
          <svg class="contact-icon" viewBox="0 0 26 26" aria-hidden="true">
            <rect width="26" height="26" rx="4" fill="var(--red)"/>
            <g fill="none" stroke="var(--navy)" stroke-width="1.5">
              <circle cx="13" cy="13" r="7.5"/>
              <ellipse cx="13" cy="13" rx="3.2" ry="7.5"/>
              <line x1="5.5" y1="13" x2="20.5" y2="13"/>
              <line x1="7" y1="9" x2="19" y2="9"/>
              <line x1="7" y1="17" x2="19" y2="17"/>
            </g>
          </svg>
          www.prairielanternpopcorn.com
        </li>
      </ul>
    </section>

    <div class="brand-mark">
      <span class="brand-dot"></span>
      <p class="brand-name">Prairie Lantern<br>Popcorn</p>
    </div>
  </div>
</body>
</html>
```